Stationery Design Project for Nimbora, Chicago

Nimbora, a street parking application which helps car drivers find a street parking spot by offering an ideal path along which to look for parking. This path is calculated by our algorithm based on data (e.g. historical data, baseball games schedule, etc.). Along this path the driver will find a spot and will also save 70% of the search time. Customer we target is reg. between 21 and 45 yo.

We envision something young, fresh, bright and original. Slightly abstract maybe. It should represent the idea and elements of finding street parking in the city, e.g. car(s), parking spot, people, city, etc. (just ideas!).

Logo is attached.

Requirement:
- Business Cards (2 Sided Full Color CMYK)
- Letterhead (1 Sided Full Color CMYK)
- Envelope (1 Sided Full Color CMYK)
- Sticker (1 Sided Full Color CMYK), round with a 2inch diameter.

Reason: We're starting to get more and more designs and need more time to look into all of them. Very exciting!! Thanks to everybody!

Hi all, we're in the process of selecting our favs. Though choices!!! Really good submissions. Will keep you posted and sorry for the delay.

Target Market(s)

Car drivers and owners between 21 and 45

Industry/Entity Type

Parking

Requirements
Must have
• Sticker should be round and include company URL nimbora.com and the new logo which we will attach soon.
Should not have
• Should not be too serious or boring.

```html
<!DOCTYPE html>
<html lang="en">
<head>
<meta charset="utf-8">
<title>Nimbora Business Cards</title>
<link rel="stylesheet" href="https://fonts.googleapis.com/css2?family=Source+Sans+3:wght@400;600;700&display=swap">
<style>
  :root {
    --page-bg: #ece7e1;
    --card-bg: #ffffff;
    --card-edge: #b9b2aa;
    --ink: #333333;
    --ink-soft: #2b2b2b;
    --brand-blue: #1d62c8;
    --band-start: #3aa2dc;
    --band-end: #2b3483;
    --rule-dark: #2a2f45;
    --divider: #9a9a9a;
    --white: #ffffff;
  }
  * { margin: 0; padding: 0; box-sizing: border-box; }
  html, body {
    width: 1200px; height: 1057px; overflow: hidden;
    background: var(--page-bg);
    font-family: "Source Sans 3", "Myriad Pro", Arial, sans-serif;
    color: var(--ink);
  }
  .card {
    position: absolute;
    width: 751px; height: 428px;
    background: var(--card-bg);
    border: 1px solid var(--card-edge);
  }
  .card--front { left: 80px; top: 71px; }
  .card--back { left: 343px; top: 548px; height: 429px; }

  .brand { position: absolute; display: flex; align-items: center; }
  .brand__dot {
    width: 134px; height: 134px; border-radius: 50%;
    background: var(--brand-blue);
    flex: none;
  }
  .brand__name {
    margin-left: 28px;
    font-size: 92px; font-weight: 600; line-height: 1;
    color: var(--ink); letter-spacing: 1px;
  }
  .card--front .brand { left: 143px; top: 38px; }
  .card--back .brand { left: 141px; top: 143px; }

  .header-rule {
    position: absolute; left: 0; right: 0; top: 219px;
    height: 3px; background: var(--rule-dark);
  }
  .name-band {
    position: absolute; left: 0; right: 0; top: 226px; height: 48px;
    background: linear-gradient(90deg, var(--band-start), var(--band-end));
    display: flex; align-items: center; justify-content: center;
    color: var(--white);
  }
  .name-band__name { font-size: 25px; font-weight: 600; }
  .name-band__title { font-size: 20px; font-weight: 400; margin-left: 5px; }

  .address {
    position: absolute; right: 363px; top: 324px;
    text-align: right; font-style: normal;
    font-size: 18px; line-height: 26px; color: var(--ink-soft);
  }
  .divider {
    position: absolute; left: 410px; top: 297px;
    width: 2px; height: 112px; background: var(--divider);
  }
  .contacts {
    position: absolute; left: 437px; top: 296px;
    list-style: none; font-size: 18px; line-height: 27px; color: var(--ink-soft);
  }
  .contacts li { display: flex; align-items: center; }
  .contacts svg { width: 13px; height: 13px; margin-right: 9px; fill: var(--ink-soft); }

  .web {
    position: absolute; left: 0; right: 0; top: 322px;
    text-align: center; font-size: 24px; letter-spacing: 2px; color: var(--ink-soft);
  }
</style>
</head>
<body>
  <section class="card card--front">
    <div class="brand">
      <span class="brand__dot"></span>
      <span class="brand__name">nimbora</span>
    </div>
    <div class="header-rule"></div>
    <div class="name-band">
      <span class="name-band__name">Your Name ,</span>
      <span class="name-band__title">Title</span>
    </div>
    <address class="address">
      Complex Name, Street Name<br>
      Area, City Name,000 000
    </address>
    <div class="divider"></div>
    <ul class="contacts">
      <li><svg viewBox="0 0 16 16" aria-hidden="true"><path d="M4 1l3 3-2 2c1 2 3 4 5 5l2-2 3 3-2 3C7 15 1 9 1 3z"/></svg>+91 12345 67890</li>
      <li><svg viewBox="0 0 16 16" aria-hidden="true"><path d="M4 0h8v16H4zM5.5 2v8h5V2zM7 12h2v2H7z"/></svg>+91 12345 67890</li>
      <li><svg viewBox="0 0 16 16" aria-hidden="true"><path d="M0 3h16v10H0zM1.5 4.5v.5L8 9l6.5-4v-.5z"/></svg>info@nimbora.com</li>
      <li><svg viewBox="0 0 16 16" aria-hidden="true"><circle cx="8" cy="8" r="7"/></svg>www.nimbora.com</li>
    </ul>
  </section>

  <section class="card card--back">
    <div class="brand">
      <span class="brand__dot"></span>
      <span class="brand__name">nimbora</span>
    </div>
    <p class="web">www.nimbora.com</p>
  </section>
</body>
</html>
```